Redesign of business card for Cedar Ridge Mechanical

We are looking for a new design for our business cards for Cedar Ridge Mechanical. We are a plumbing & HVAC construction company, operating on the West Coast of Canada and USA. Logo attached.
Industry/Entity Type
Construction - Plumbing & HVAC
Contact Information for Business Card
Name, address, phone numbers, email, website address
Look and feel
Each slider illustrates characteristics of the customer's brand and the style your logo design should communicate.

```html
<!DOCTYPE html>
<html lang="en">
<head>
<meta charset="utf-8">
<title>Cedar Ridge Mechanical – Business Card</title>
<link href="https://fonts.googleapis.com/css2?family=Open+Sans:wght@400;600;700&display=swap" rel="stylesheet">
<style>
  :root{
    --page-bg:#d6d1ca;
    --card-frost-top:#efedea;
    --card-frost-bottom:#e2ded9;
    --panel-dark:#141414;
    --panel-mid:#262626;
    --silver:#9a9895;
    --text-gold:#cdbb9c;
    --text-light:#d9cdb8;
    --ink:#1c1c1c;
  }
  *{margin:0;padding:0;box-sizing:border-box}
  html,body{width:1200px;height:1047px;overflow:hidden}
  body{background:var(--page-bg);position:relative;font-family:"Open Sans",Arial,sans-serif}
  .card{
    position:absolute;left:161px;top:283px;width:878px;height:480px;
    border-radius:22px;overflow:hidden;
    background:linear-gradient(180deg,var(--card-frost-top),var(--card-frost-bottom));
    box-shadow:0 10px 30px rgba(0,0,0,.18);
  }
  .card-panel{position:absolute;left:0;top:0;width:878px;height:480px}
  .contact{position:absolute;left:18px;top:150px;color:var(--text-light)}
  .contact-name{font-size:30px;font-weight:700;letter-spacing:.5px;color:var(--text-gold);line-height:1.1}
  .contact-title{font-size:21px;font-weight:400;margin-top:4px}
  .contact-address{font-size:23px;line-height:30px;margin-top:36px}
  .contact-lines{list-style:none;margin-top:38px;font-size:23px;line-height:30px}
  .contact-lines li{display:flex;align-items:center;gap:6px}
  .contact-lines svg{width:18px;height:18px;flex:none}
  .brand{position:absolute;left:478px;top:150px;display:flex;align-items:center;gap:16px}
  .brand-square{width:34px;height:34px;background:var(--ink)}
  .brand-name{font-size:30px;font-weight:700;color:var(--ink);letter-spacing:1px;line-height:1.15;text-transform:uppercase}
</style>
</head>
<body>
  <div class="card">
    <svg class="card-panel" viewBox="0 0 878 480" aria-hidden="true">
      <defs>
        <linearGradient id="panelShade" x1="0" y1="0" x2="1" y2="1">
          <stop offset="0" stop-color="var(--panel-mid)"/>
          <stop offset="1" stop-color="var(--panel-dark)"/>
        </linearGradient>
      </defs>
      <path d="M0,0 H362 C318,40 330,130 365,205 C405,290 455,370 430,480 H0 Z" fill="#8f8d8a" opacity=".55"/>
      <path d="M362,0 C318,40 330,130 365,205 C405,290 455,370 430,480" fill="none" stroke="var(--silver)" stroke-width="3"/>
      <path d="M0,0 H350 C306,40 316,130 350,205 C390,290 430,370 405,480 H0 Z" fill="url(#panelShade)"/>
    </svg>

    <div class="contact">
      <p class="contact-name">DANIEL HALE</p>
      <p class="contact-title">Managing Director</p>
      <p class="contact-address">Your address, City<br>State, Zip 1234</p>
      <ul class="contact-lines">
        <li><svg viewBox="0 0 24 24"><path fill="currentColor" d="M6.6 10.8a15 15 0 0 0 6.6 6.6l2.2-2.2c.3-.3.7-.4 1-.2 1.1.4 2.3.6 3.6.6.6 0 1 .4 1 1V20c0 .6-.4 1-1 1A17 17 0 0 1 3 4c0-.6.4-1 1-1h3.5c.6 0 1 .4 1 1 0 1.3.2 2.5.6 3.6.1.3 0 .7-.2 1z"/></svg>123 456 789</li>
        <li><svg viewBox="0 0 24 24"><path fill="currentColor" d="M3 5h18v14H3zm2 2v.5l7 4.5 7-4.5V7zm0 2.9V17h14V9.9l-7 4.5z"/></svg>info@yourmail.com</li>
        <li><svg viewBox="0 0 24 24"><circle cx="12" cy="12" r="9" fill="none" stroke="currentColor" stroke-width="2"/><path d="M3 12h18M12 3c3 3 3 15 0 18M12 3c-3 3-3 15 0 18" fill="none" stroke="currentColor" stroke-width="1.6"/></svg>www.yourwebsite.com</li>
      </ul>
    </div>

    <div class="brand">
      <span class="brand-square"></span>
      <p class="brand-name">Cedar Ridge<br>Mechanical</p>
    </div>
  </div>
</body>
</html>
```